Coffee House With Cycling Theme Wants Business Cards

We want to create a business card for a coffee house that has a cycling theme. We expect to use the current logo on one side of the business card and we have been considering adding the words 'COFFEE HOUSE' underneath (see example). For the other side of the business card we want an interesting design with tag-line, address and social media links (the normal business card stuff). See examples provided but we are not fixed on having it exactly as shown, we are very open to great creative ideas. Please note our logo has the initials ‘KR' in orange embedded in the design and this must be retained. However, you can play with the words COFFEE HOUSE as well as use the orange color on the backside of the business card, as you see fit. For an image on the backside of the business card it can be a photo, hand-drawn or whatever but it must visually combine coffee and cycling in some way. The interior of the Coffee House will be reclaimed wood, rustic and have an urban feel to it with cycling artifacts hanging from the walls/ceiling, etc. Finally, it would be beneficial if the business card design elements can be easily used on flyers and other promotional assets. Good luck, we are looking forward to seeing your creative ideas.

Target Market(s)

Coffee lovers and cycling fans

Contact Information for Business Card

See project description.

Colors

Designer to choose colors to be used in the design.

Requirements
Must have
• Must use the current logo provided and combine a coffee and bike theme.
Nice to have
• Orange is used in current logo and could be used as an accent color on the backside of the business card.

```html
<!DOCTYPE html>
<html lang="en">
<head>
<meta charset="utf-8">
<title>KR Coffee House – Business Card</title>
<link href="https://fonts.googleapis.com/css2?family=Open+Sans:wght@400;600&display=swap" rel="stylesheet">
<style>
  :root {
    --backdrop: #9c9c9c;
    --orange: #f26a2a;
    --orange-light: #f3824a;
    --charcoal: #3c3c3c;
    --ink: #1e1e1e;
    --white: #ffffff;
    --social-a: #3b5998;
    --social-b: #e1306c;
  }
  * { box-sizing: border-box; margin: 0; padding: 0; }
  html, body {
    width: 1200px; height: 930px; overflow: hidden;
    background: var(--backdrop);
    font-family: "Open Sans", Arial, sans-serif;
  }
  .canvas { position: relative; width: 1200px; height: 930px; }

  .card {
    position: absolute;
    width: 540px; height: 310px;
    border-radius: 22px;
    overflow: hidden;
    box-shadow: 0 8px 18px rgba(0,0,0,0.25);
  }

  /* Front */
  .card--front {
    left: 90px; top: 110px;
    background: linear-gradient(120deg, var(--orange) 0%, var(--orange-light) 50%, var(--orange) 100%);
  }
  .front__brand {
    position: absolute; left: 0; right: 0; top: 92px;
    text-align: center; color: var(--white); font-weight: 400;
    letter-spacing: 2px;
  }
  .front__initials { font-size: 72px; line-height: 1; }
  .front__name { font-size: 34px; margin-top: 8px; }

  /* Back */
  .card--back { left: 570px; top: 500px; background: var(--white); }
  .back__shape { position: absolute; inset: 0; width: 100%; height: 100%; }

  .back__brand {
    position: absolute; left: 34px; top: 60px;
    color: var(--ink); font-weight: 400; letter-spacing: 1px;
  }
  .back__initials { font-size: 52px; line-height: 1; }
  .back__name { font-size: 24px; margin-top: 4px; }

  .social { position: absolute; left: 34px; top: 168px; list-style: none; }
  .social li {
    display: flex; align-items: center; gap: 8px;
    font-size: 13px; color: var(--ink); margin-bottom: 8px;
  }
  .social__mark { width: 14px; height: 14px; border-radius: 3px; }
  .social__mark--a { background: var(--social-a); }
  .social__mark--b { background: var(--social-b); }

  .contact {
    position: absolute; right: 28px; top: 70px;
    text-align: right; color: var(--white);
  }
  .contact__person { font-size: 19px; font-weight: 600; letter-spacing: 1px; }
  .contact__role { font-size: 11px; margin-bottom: 14px; }
  .contact__line { font-size: 11.5px; line-height: 1.55; display: flex; justify-content: flex-end; align-items: center; gap: 6px; }
  .contact__gap { height: 10px; }
  .contact__icon { width: 10px; height: 10px; }
</style>
</head>
<body>
<main class="canvas">

  <section class="card card--front" aria-label="Business card front">
    <div class="front__brand">
      <div class="front__initials">KR</div>
      <div class="front__name">COFFEE HOUSE</div>
    </div>
  </section>

  <section class="card card--back" aria-label="Business card back">
    <svg class="back__shape" viewBox="0 0 540 310" preserveAspectRatio="none" aria-hidden="true">
      <path d="M455 0 C360 10 345 150 270 225 C215 275 120 262 0 250 L0 310 L540 310 L540 0 Z" fill="var(--orange)"/>
      <path d="M462 0 C368 12 352 150 276 228 C222 280 120 268 0 257"
            fill="none" stroke="var(--charcoal)" stroke-width="7"/>
      <path d="M448 0 C356 8 340 150 266 222 C212 270 120 256 0 245"
            fill="none" stroke="var(--white)" stroke-width="3"/>
    </svg>

    <div class="back__brand">
      <div class="back__initials">KR</div>
      <div class="back__name">COFFEE HOUSE</div>
    </div>

    <ul class="social">
      <li><span class="social__mark social__mark--a"></span>krcoffeehouse.com</li>
      <li><span class="social__mark social__mark--b"></span>krcoffeehouse.com</li>
    </ul>

    <div class="contact">
      <div class="contact__person">DANIEL HART</div>
      <div class="contact__role">Director</div>
      <div class="contact__line">42 Harbour Lane,</div>
      <div class="contact__line">Lyttelton, NZ, 8082</div>
      <div class="contact__gap"></div>
      <div class="contact__line">(555) 014-2290
        <svg class="contact__icon" viewBox="0 0 10 10" aria-hidden="true"><path d="M2 1 L4 1 L4.6 3 L3.4 3.8 C4 5.2 4.8 6 6.2 6.6 L7 5.4 L9 6 L9 8 C9 8.6 8.6 9 8 9 C4.2 9 1 5.8 1 2 C1 1.4 1.4 1 2 1 Z" fill="var(--white)"/></svg>
      </div>
      <div class="contact__line">info@krcoffeehouse.com
        <svg class="contact__icon" viewBox="0 0 10 10" aria-hidden="true"><rect x="1" y="2.5" width="8" height="5.5" fill="none" stroke="var(--white)" stroke-width="1"/><path d="M1 2.5 L5 5.5 L9 2.5" fill="none" stroke="var(--white)" stroke-width="1"/></svg>
      </div>
      <div class="contact__line">www.krcoffeehouse.com
        <svg class="contact__icon" viewBox="0 0 10 10" aria-hidden="true"><circle cx="5" cy="5" r="4" fill="none" stroke="var(--white)" stroke-width="1"/><path d="M1 5 H9 M5 1 C3 3 3 7 5 9 C7 7 7 3 5 1" fill="none" stroke="var(--white)" stroke-width="0.8"/></svg>
      </div>
    </div>
  </section>

</main>
</body>
</html>
```